Website Design for The Elder Nook

Please design and code a new website.
Here are the sites I like best:
http://www.voyaglint.com/alternate/
http://www.wheelgiftbay.org
Please make it similar but look at the competitor site (below) for images and wording. This is NOT a car donation site. It's a senior lead placement site like https://www.kinhavenfinder.com. I just like this sites above as a lead generation sites.
Competitor site:
https://www.kinhavenfinder.com (use ideas / verbiage from this site)
Updates
Competitor site:
Coding
Coded - Design and coding required
Number of Pages Required
1 page
Look and feel
Each slider illustrates characteristics of the customer's brand and the style your logo design should communicate.

```html
<!DOCTYPE html>
<html lang="en">
<head>
<meta charset="utf-8">
<title>The Elder Nook — Senior Living Advice</title>
<link href="https://fonts.googleapis.com/css2?family=Lustria&family=Nunito+Sans:wght@300;400;600&display=swap" rel="stylesheet">
<style>
:root{
  --blue:#1462b8;
  --blue-deep:#0d3f80;
  --green:#8cc63f;
  --text:#333;
  --muted:#777;
  --line:#e2e2e2;
  --white:#fff;
}
*{box-sizing:border-box;margin:0;padding:0}
html,body{width:1200px;height:3040px;overflow:hidden}
body{font-family:"Nunito Sans",sans-serif;color:var(--text);background:var(--white);position:relative}
.serif{font-family:"Lustria",serif}
section,header,nav,footer{position:absolute;left:0;width:1200px}
.abs{position:absolute}
.c-green{color:var(--green)}
.c-blue{color:var(--blue)}
.btn{position:absolute;background:var(--green);color:#fff;font-family:"Lustria",serif;font-size:16px;display:flex;align-items:center;justify-content:center;border-radius:2px}
h2.section-title{position:absolute;left:0;width:1200px;text-align:center;font-family:"Lustria",serif;font-weight:400;font-size:30px}

/* header */
.site-header{top:0;height:91px}
.brand{left:88px;top:28px;display:flex;align-items:center;gap:8px;font-family:"Lustria",serif;font-size:24px;color:var(--blue)}
.brand-dot{width:14px;height:14px;border-radius:50%;background:var(--green)}
.call{left:626px;top:22px;display:flex;align-items:center;gap:10px}
.call small{display:block;font-family:"Lustria",serif;font-size:11px;color:#555}
.call strong{display:block;font-weight:400;font-size:23px;color:#222;line-height:1.1}
.badge{left:858px;top:22px;width:95px;height:46px;background:var(--blue);border-radius:3px}
.lang{left:1010px;top:28px;width:102px;height:34px;border:1px solid #ddd;display:flex;align-items:center;justify-content:center;gap:6px;font-size:12px}
.flag{width:32px;height:18px;background:linear-gradient(#b22 0 15%,#fff 15% 30%,#b22 30% 45%,#fff 45% 60%,#b22 60% 75%,#fff 75% 90%,#b22 90%);position:relative}
.flag::before{content:"";position:absolute;left:0;top:0;width:14px;height:10px;background:#2a3f8f}

.main-nav{top:91px;height:42px;background:var(--blue)}
.main-nav ul{list-style:none;position:absolute;left:88px;display:flex;height:42px}
.main-nav li{font-family:"Lustria",serif;font-size:12.5px;color:#fff;padding:0 20px;display:flex;align-items:center;border-right:1px solid rgba(255,255,255,.2)}
.main-nav li.active{background:#0f4f98;border-bottom:3px solid var(--green)}

/* hero */
.hero{top:133px;height:573px}
.hero-photo{position:absolute;inset:0;background:linear-gradient(100deg,#c9b49b 0%,#e4dcd3 35%,#f3eee8 55%,#e9dccd 80%,#d8c4ad 100%)}
.hero-text{left:420px;top:250px;width:370px;text-align:center;font-family:"Lustria",serif;font-size:28px;line-height:1.5;color:#111}
.inquiry{left:782px;top:77px;width:330px;height:419px;background:var(--blue);box-shadow:0 14px 14px -10px rgba(0,0,0,.35)}
.inquiry-head{position:absolute;left:10px;top:10px;width:310px;height:80px;background:var(--green);clip-path:polygon(0 0,100% 0,100% 80%,50% 100%,0 80%);color:#fff;font-family:"Lustria",serif;font-size:25px;text-align:center;padding-top:24px}
.field{position:absolute;left:12px;width:306px;height:41px;background:var(--blue-deep);border:1px solid #2a6bbd;display:flex;align-items:center;color:#fff;font-size:13px}
.field .ico{width:40px;height:100%;border-right:1px solid #2a6bbd;display:flex;align-items:center;justify-content:center}
.field span{padding-left:16px}
.field.msg{height:70px;align-items:flex-start}
.field.msg .ico{height:100%;align-items:flex-start;padding-top:13px}
.field.msg span{padding-top:12px}

/* support */
.support{top:706px;height:545px}
.support p.lead{position:absolute;left:200px;width:800px;top:124px;text-align:center;font-size:13.5px;line-height:1.75;color:#444}
.card{position:absolute;top:193px;width:172px;height:181px;border:1px solid var(--line);box-shadow:0 3px 6px rgba(0,0,0,.06);text-align:center;font-size:17px;color:#333;line-height:1.25;padding:0 10px}
.card.narrow{padding:0 36px}
.card svg{margin:22px auto 8px;display:block}
.nocost{top:444px;font-family:"Lustria",serif;font-size:24px;left:142px}
.nocost-text{top:420px;left:426px;font-size:16.5px;line-height:1.55;color:#333}
.nocost-call{top:428px;left:869px;font-size:21px;color:var(--blue)}

/* advisor */
.advisor{top:1251px;height:480px;background:linear-gradient(90deg,#1a5fae,#1f66b6 50%,#1a5fae);color:#fff}
.advisor .portraits{position:absolute;inset:0;background:repeating-linear-gradient(90deg,rgba(255,255,255,0) 0 150px,rgba(0,0,0,.05) 150px 180px)}
.advisor h2{color:#fff;top:77px;font-size:29px}
.advisor p.lead{position:absolute;top:126px;width:1200px;text-align:center;font-size:14.5px}
.feature{position:absolute;top:174px;width:200px;text-align:center;font-size:15.5px;line-height:1.3}
.ring{width:97px;height:97px;border:1.5px solid #fff;border-radius:50%;margin:0 auto 14px;display:flex;align-items:center;justify-content:center}
.search{left:299px;top:350px;width:603px;height:45px;background:#fff;border-radius:2px}
.search span{position:absolute;left:20px;top:13px;color:#333;font-size:14px}
.search .btn{left:377px;top:3px;width:222px;height:39px}

/* testimonials */
.testimonials{top:1731px;height:484px}
.quote{position:absolute;top:139px;width:283px;height:148px;border:1px solid var(--line);padding:10px 17px;font-size:12.5px;line-height:21.5px;color:#777}
.quote .mark{position:absolute;right:16px;bottom:8px;font-family:"Lustria",serif;font-size:70px;line-height:.6;color:#eee}
.person{position:absolute;top:266px;display:flex;align-items:center;gap:22px;font-family:"Lustria",serif;font-size:14.5px;color:#333;z-index:1}
.avatar{width:70px;height:70px;border-radius:50%;border:3px solid var(--blue);background:radial-gradient(circle at 50% 40%,#e8d5c3,#b79b82);box-shadow:0 0 0 3px #fff}
.testimonials .btn{left:496px;top:361px;width:207px;height:38px}

/* veteran */
.veteran{top:2215px;height:290px;background:linear-gradient(180deg,#3a4a6a 0%,#2a2a3a 40%,#4a2228 75%,#1f1a1c 100%);color:#fff;text-align:center}
.veteran h2{color:#fff;top:70px;font-size:25px}
.veteran p{position:absolute;top:113px;width:1200px;font-size:14.5px;line-height:1.7}
.veteran .btn{left:536px;top:176px;width:128px;height:38px}

/* states */
.states{top:2505px;height:365px}
.states h2{top:82px}
.state-col{position:absolute;top:138px;list-style:none;font-size:13px;line-height:21.8px;color:#333}
.state-col li::before{content:"› "}

/* footer */
.site-footer{top:2870px;height:170px;background:var(--blue);color:#fff}
.foot-nav{position:absolute;top:47px;left:0;width:1200px;display:flex;justify-content:center;gap:34px;list-style:none;font-family:"Lustria",serif;font-size:11px}
.foot-rule{position:absolute;top:113px;left:142px;width:916px;height:1px;background:rgba(255,255,255,.2)}
.copy{position:absolute;top:133px;left:142px;font-size:13px}
.socials{position:absolute;top:130px;left:945px;display:flex;gap:6px}
.socials span{width:24px;height:24px;border-radius:50%;border:1.5px solid #fff;background:#3b78c6}
</style>
</head>
<body>

<header class="site-header">
  <div class="abs brand"><span class="brand-dot"></span>The Elder Nook</div>
  <div class="abs call">
    <svg width="34" height="34" viewBox="0 0 24 24" fill="none" stroke="#1462b8" stroke-width="1.4"><path d="M5 3h4l2 5-2.5 1.5a11 11 0 0 0 6 6L16 13l5 2v4a2 2 0 0 1-2 2A17 17 0 0 1 3 5a2 2 0 0 1 2-2z"/><path d="M15 3a6 6 0 0 1 6 6M15 6.5a2.5 2.5 0 0 1 2.5 2.5"/></svg>
    <div><small>Talk to a local advisor for FREE</small><strong>(555) 218-4630</strong></div>
  </div>
  <div class="abs badge" role="img" aria-label="Accreditation badge"></div>
  <div class="abs lang">EN : <span class="flag"></span> ⌄</div>
</header>

<nav class="main-nav">
  <ul>
    <li class="active">ASSISTED LIVING</li>
    <li>MEMORY CARE</li>
    <li>NURSING HOMES</li>
    <li>MORE LIVING OPTIONS ⌄</li>
    <li>PLANNING &amp; ADVICE</li>
    <li>HOW OUR SERVICE WORKS</li>
  </ul>
</nav>

<section class="hero">
  <div class="hero-photo" role="img" aria-label="Photo of a happy senior couple running hand in hand along a sunny beach"></div>
  <div class="abs hero-text">You know your family.<br>We know <em>Senior Living</em>.</div>
  <form class="abs inquiry">
    <div class="inquiry-head">Quick Inquiry</div>
    <div class="field" style="top:104px"><div class="ico"><svg width="12" height="12" viewBox="0 0 12 12" fill="#fff"><circle cx="6" cy="3.5" r="2.5"/><path d="M1 12a5 5 0 0 1 10 0z"/></svg></div><span>Name</span></div>
    <div class="field" style="top:157px"><div class="ico"><svg width="12" height="12" viewBox="0 0 24 24" fill="#fff"><path d="M5 2h4l2 5-2.5 1.5a11 11 0 0 0 6 6L16 12l5 2v4a2 2 0 0 1-2 2A17 17 0 0 1 3 4a2 2 0 0 1 2-2z"/></svg></div><span>Phone</span></div>
    <div class="field" style="top:210px"><div class="ico"><svg width="13" height="10" viewBox="0 0 13 10"><rect width="13" height="10" fill="#fff"/><path d="M0 0l6.5 5L13 0" stroke="#0d3f80" fill="none"/></svg></div><span>Email</span></div>
    <div class="field msg" style="top:263px"><div class="ico"><svg width="14" height="12" viewBox="0 0 14 12" fill="#fff"><ellipse cx="6" cy="5" rx="6" ry="4"/><path d="M2 8l-1 4 4-2z"/></svg></div><span>Message</span></div>
    <div class="btn" style="left:12px;top:352px;width:306px;height:38px;font-size:15px">Submit Now</div>
  </form>
</section>

<section class="support">
  <h2 class="section-title" style="top:78px"><span class="c-green">The Support You Need To</span> <span class="c-blue">Make The Right Choice</span></h2>
  <p class="lead">Lorem ipsum dolor sit amet, consectetuer adipiscing elit, sed diam nonummy nibh euismod tincidunt ut laoreet dolore magna aliquam erat volutpat. Ut wisi enim ad minim veniam, quis nostrud exerci tation ullamcorper suscipit.</p>

  <div class="card" style="left:142px"><svg width="48" height="56" viewBox="0 0 48 56" fill="none" stroke="#8cc63f" stroke-width="2"><circle cx="24" cy="14" r="9"/><path d="M8 54V36a8 8 0 0 1 8-8h16a8 8 0 0 1 8 8v18M20 28l4 10 4-10M16 54V42M32 54V42"/></svg>Dedicated local advisor</div>
  <div class="card" style="left:328px"><svg width="52" height="56" viewBox="0 0 52 56" fill="none" stroke="#8cc63f" stroke-width="2"><path d="M4 26L26 4l22 22M10 20v34h32V20"/><rect x="20" y="36" width="12" height="18"/><rect x="21" y="18" width="10" height="10"/></svg>Hand-picked list of communities to match your needs</div>
  <div class="card" style="left:514px"><svg width="52" height="56" viewBox="0 0 52 56" fill="none" stroke="#8cc63f" stroke-width="2"><circle cx="26" cy="22" r="10"/><path d="M26 16v12M23 19h5a2 2 0 0 1 0 4h-4a2 2 0 0 0 0 4h5M26 2v6M20 4l1 4M32 4l-1 4M4 44h14l8 4h14l8-6M4 54h30l14-12"/></svg>Full details and pricing</div>
  <div class="card narrow" style="left:701px"><svg width="52" height="56" viewBox="0 0 52 56" fill="none" stroke="#8cc63f" stroke-width="2"><rect x="2" y="8" width="48" height="46"/><path d="M2 18h48M14 2v10M38 2v10M10 26h32v22H10zM18 26v22M26 26v22M34 26v22M10 33h32M10 41h32"/></svg>Help scheduling tours</div>
  <div class="card narrow" style="left:887px"><svg width="62" height="56" viewBox="0 0 62 56" fill="none" stroke="#8cc63f" stroke-width="2"><path d="M10 8h30v32H10zM40 18h12l8 12v10H40M2 16h14M4 24h12M6 32h10"/><circle cx="20" cy="44" r="5"/><circle cx="48" cy="44" r="5"/></svg>Move in support</div>

  <div class="abs nocost serif"><span class="c-green">There's</span> <span class="c-blue">No Cost To You.</span></div>
  <div class="abs nocost-text">We work with over 20,000 senior living communities.<br>Our community partners pay us for placement services.</div>
  <div class="abs nocost-call">Call (555) 218-4630</div>
</section>

<section class="advisor">
  <div class="portraits" role="img" aria-label="Row of smiling advisors tinted in blue behind the section"></div>
  <h2 class="section-title">Your local advisor informs. You decide.</h2>
  <p class="lead">Lorem ipsum dolor sit amet, consectetuer adipiscing elit, sed diam nonummy nibh euismod tincidunt ut laoreet.</p>
  <div class="feature" style="left:240px"><div class="ring"><svg width="30" height="62" viewBox="0 0 30 62" fill="none" stroke="#fff" stroke-width="1.8"><circle cx="15" cy="14" r="12"/><path d="M15 26v34"/></svg></div>Insider's tips for the area near you</div>
  <div class="feature" style="left:500px"><div class="ring"><svg width="54" height="48" viewBox="0 0 54 48" fill="none" stroke="#fff" stroke-width="2"><path d="M27 46L5 24A12 12 0 0 1 27 8a12 12 0 0 1 22 16z"/></svg></div>Advice tailored to your unique situation</div>
  <div class="feature" style="left:760px"><div class="ring"><svg width="52" height="42" viewBox="0 0 52 42" fill="none" stroke="#fff" stroke-width="2"><circle cx="5" cy="5" r="4"/><circle cx="5" cy="21" r="4"/><circle cx="5" cy="37" r="4"/><path d="M16 5h34M16 21h34M16 37h34"/></svg></div>Time saving know-how and resources</div>
  <div class="abs search"><span>Enter city or postal code</span><div class="btn">Find an advisor near you</div></div>
</section>

<section class="testimonials">
  <h2 class="section-title" style="top:80px"><span class="c-green">93% Of Our Customers</span> <span class="c-blue">Recommend Our Service</span></h2>

  <div class="quote" style="left:142px">Lorem ipsum dolor sit amet, consectetuer adipiscing elit, sed diam nonummy nibh euismod tincidunt ut laoreet dolore magna aliquam erat volutpat. Ut wisi enim ad minim veniam, quis nostrud.<span class="mark">”</span></div>
  <div class="person" style="left:150px"><div class="avatar" role="img" aria-label="Portrait of customer Mara Quill"></div>Mara Quill</div>

  <div class="quote" style="left:458px">Lorem ipsum dolor sit amet, consectetuer adipiscing elit, sed diam nonummy nibh euismod tincidunt ut laoreet dolore magna aliquam erat volutpat. Ut wisi enim ad minim veniam, quis nostrud.<span class="mark">”</span></div>
  <div class="person" style="left:467px"><div class="avatar" role="img" aria-label="Portrait of customer Owen Hart"></div>Owen Hart</div>

  <div class="quote" style="left:775px">Lorem ipsum dolor sit amet, consectetuer adipiscing elit, sed diam nonummy nibh euismod tincidunt ut laoreet dolore magna aliquam erat volutpat. Ut wisi enim ad minim veniam, quis nostrud.<span class="mark">”</span></div>
  <div class="person" style="left:784px"><div class="avatar" role="img" aria-label="Portrait of customer Lena Brooks"></div>Lena Brooks</div>

  <div class="btn">See More Testimonials</div>
</section>

<section class="veteran" role="img" aria-label="Waving flag background in dark blue and red tones">
  <h2 class="section-title">Access Up To $2,000 Per Month In Veteran's Aid</h2>
  <p>We work with Veterans every day. Most veteran families do not know of a key benefit available to them and their families.<br>It's called the Veteran's Aid and Attendance benefit. This benefit can help pay for senior living and home care.</p>
  <div class="btn">Learn More</div>
</section>

<section class="states">
  <h2 class="section-title"><span class="c-green">Senior Assisted</span> <span class="c-blue">Living by State</span></h2>
  <ul class="state-col" style="left:159px"><li>Alabama</li><li>Arizona</li><li>Arkansas</li><li>California</li><li>Colorado</li><li>Connecticut</li><li>Delaware</li></ul>
  <ul class="state-col" style="left:301px"><li>District of Columbia</li><li>Florida</li><li>Georgia</li><li>Hawaii</li><li>Idaho</li><li>Illinois</li><li>Indiana</li></ul>
  <ul class="state-col" style="left:486px"><li>Iowa</li><li>Kansas</li><li>Kentucky</li><li>Louisiana</li><li>Maine</li><li>Maryland</li><li>Massachusetts</li></ul>
  <ul class="state-col" style="left:644px"><li>Michigan</li><li>Minnesota</li><li>Mississippi</li><li>Missouri</li><li>Montana</li><li>Nebraska</li><li>Nevada</li></ul>
  <ul class="state-col" style="left:780px"><li>New Hampshire</li><li>New Jersey</li><li>New Mexico</li><li>New York</li><li>North Carolina</li><li>North Dakota</li><li>Ohio</li></ul>
  <ul class="state-col" style="left:950px"><li>Oklahoma</li><li>Oregon</li><li>Pennsylvania</li><li>Rhode Island</li><li>South Carolina</li><li>South Dakota</li><li>Tennessee</li></ul>
</section>

<footer class="site-footer">
  <ul class="foot-nav">
    <li>ASSISTED LIVING</li><li>MEMORY CARE</li><li>NURSING HOMES</li><li>MORE LIVING OPTIONS ⌄</li><li>PLANNING &amp; ADVICE</li><li>HOW OUR SERVICE WORKS</li>
  </ul>
  <div class="foot-rule"></div>
  <div class="copy">Copyright 2019 The Elder Nook. All Rights Reserved.</div>
  <div class="socials" aria-label="Social links"><span></span><span></span><span></span><span></span></div>
</footer>

</body>
</html>
```